New business card for a regional office of a US M&A company

We need business card for a finance company, office based in Hong Kong , our Head office is in US, our business is to Merge and acquires companies , the new office will be a regional office for the Asia Pacific region. We want to use the head office logo as attached ( but don't have to be exactly the same, can be a variation to it) as a base and then add Asia Pacific alongside the logo.
We would prefer to have be bilingual Eng + Chinese, although we don't really have Chinese company name .

Industry/Entity Type

Business

Contact Information for Business Card

Clara Jo Tsang
 

VP,
APAC M&A Operations
Orin Vantage Asia Pacific Limited
 
Unit 1407, K18
18 Tai Lok Shan Road, 
Hong Kong 
 
M: +852 6038 1742
T : +852 2836 4100
F : +852 2836 4177
VOIP: 4158
 
cjtsang@orinvantage.com

Font styles to use
Serif
Sans Serif

Colors

Designer to choose colors to be used in the design.

Requirements
Must have
• APAC Office

```html
<!DOCTYPE html>
<html lang="en">
<head>
<meta charset="utf-8">
<title>Orin Vantage – Business Card</title>
<link href="https://fonts.googleapis.com/css2?family=Open+Sans:wght@700&family=Roboto:wght@400&family=Roboto+Condensed:wght@500&display=swap" rel="stylesheet">
<style>
  :root {
    --backdrop: #2b2b2c;
    --card-navy: #0f2840;
    --brand-cyan: #22a7d3;
    --text-light: #e3e8ee;
    --tab-white: #ffffff;
  }
  * { margin: 0; padding: 0; box-sizing: border-box; }
  html, body {
    width: 1200px; height: 960px; overflow: hidden;
    background: var(--backdrop);
  }
  .canvas { position: relative; width: 1200px; height: 960px; }

  .card {
    position: absolute;
    background: var(--card-navy);
    box-shadow: 0 2px 6px rgba(0,0,0,0.45);
  }
  .card-front { left: 322px; top: 108px; width: 602px; height: 340px; }
  .card-back  { left: 320px; top: 493px; width: 600px; height: 342px; }

  .brand-name {
    font-family: "Open Sans", sans-serif;
    font-weight: 700;
    color: var(--brand-cyan);
    white-space: nowrap;
    position: absolute;
    letter-spacing: -0.5px;
  }
  .card-front .brand-name {
    left: 0; right: 0; top: 180px;
    text-align: center; font-size: 50px; line-height: 1;
  }
  .website {
    position: absolute; left: 0; right: 0; top: 284px;
    text-align: center;
    font-family: "Roboto", sans-serif; font-size: 14px;
    letter-spacing: 6px; color: var(--text-light);
  }

  .accent-tab {
    position: absolute; left: 405px; top: 0;
    width: 80px; height: 58px; background: var(--tab-white);
  }
  .card-back .brand-name {
    right: 34px; top: 113px; font-size: 36px; line-height: 1;
  }

  .holder-name {
    position: absolute; left: 34px; top: 24px;
    font-family: "Roboto Condensed", sans-serif; font-weight: 500;
    font-size: 21px; color: var(--brand-cyan); text-transform: uppercase;
  }
  .holder-title {
    position: absolute; left: 36px; top: 50px;
    font-family: "Roboto", sans-serif; font-size: 14px; color: var(--text-light);
  }
  .contact-block {
    position: absolute; left: 35px; top: 123px;
    font-family: "Roboto", sans-serif; font-size: 14.5px;
    line-height: 19px; color: var(--text-light);
  }
  .address { margin-bottom: 9px; }
  .phone-line { display: flex; align-items: center; gap: 8px; }
  .phone-line svg { width: 15px; height: 15px; fill: var(--brand-cyan); flex: none; }
  .voip { margin-top: 10px; }
</style>
</head>
<body>
<div class="canvas">

  <section class="card card-front">
    <div class="brand-name">ORIN VANTAGE</div>
    <div class="website">www.orinvantage.com</div>
  </section>

  <section class="card card-back">
    <div class="accent-tab"></div>
    <div class="brand-name">ORIN VANTAGE</div>

    <div class="holder-name">Clara Jo Tsang</div>
    <div class="holder-title">VP</div>

    <div class="contact-block">
      <div class="address">
        APAC M&amp;A Operations<br>
        Orin Vantage Asia Pacific Limited<br>
        Unit 1407, K18<br>
        18 Tai Lok Shan Road<br>
        Hong Kong
      </div>
      <div class="phone-line">
        <svg viewBox="0 0 16 16" aria-hidden="true"><path d="M3.2 1.5l2.3-.4 1.4 3.3-1.5 1.2c.8 1.7 2.1 3 3.8 3.8l1.2-1.5 3.3 1.4-.4 2.3c-.2.8-.9 1.3-1.7 1.2C6.5 12.4 2.3 8.2 2 3.2c0-.8.5-1.5 1.2-1.7z"/></svg>
        <span>+852 2836 4100</span>
      </div>
      <div class="phone-line">
        <svg viewBox="0 0 16 16" aria-hidden="true"><path d="M4.5 0.5h7c.6 0 1 .4 1 1v13c0 .6-.4 1-1 1h-7c-.6 0-1-.4-1-1v-13c0-.6.4-1 1-1zm.6 2v9.5h5.8V2.5zM8 12.8a.8.8 0 100 1.6.8.8 0 000-1.6z"/></svg>
        <span>+852 6038 1742</span>
      </div>
      <div class="phone-line">
        <svg viewBox="0 0 16 16" aria-hidden="true"><path d="M4 1h6.5L12 2.5V6H4zM1.5 7h13c.6 0 1 .4 1 1v5c0 .6-.4 1-1 1h-13c-.6 0-1-.4-1-1V8c0-.6.4-1 1-1zm2 4v3h9v-3z"/></svg>
        <span>+852 2836 4177</span>
      </div>
      <div class="voip">VOIP: 4158</div>
    </div>
  </section>

</div>
</body>
</html>
```